Ward Compass Business Card Design*

We need a business card design for our company Ward Compass. Our company is specialized in providing online consulting services regarding medical institutions, hospitals and doctors. We work with patients worldwide looking to choose between healthcare providers. We have a website you may use as a reference, where we list doctors and clinics worldwide. So we target Medical providers as well as patients worldwide.
Target Market(s)
Medical Providers and patients around the world
Industry/Entity Type
Medical
Contact Information for Business Card
Salwa Kettani
CEO
+90 612 348 2175
info@wardcompass.example
www.wardcompass.example
14 Annakhil 7 H.R.B. Rabat, Morocco
Requirements
Must have
- Company logo/name on one full side, personal info and smaller logo and company name on the other side.
Nice to have
- Smart and elegant design

```html
<!DOCTYPE html>
<html lang="en">
<head>
<meta charset="utf-8">
<title>Ward Compass — Business Card</title>
<link rel="stylesheet" href="https://fonts.googleapis.com/css2?family=Poppins:wght@400;500&family=Roboto:wght@400&display=swap">
<style>
  :root {
    --backdrop: #e4e4e4;
    --card: #ffffff;
    --navy: #1d3f6e;
    --grey-text: #555a60;
    --soft-grey: #7a7f85;
    --faint-shape: #e8ecf2;
  }
  * { margin: 0; padding: 0; box-sizing: border-box; }
  html, body {
    width: 1200px; height: 1200px; overflow: hidden;
    background: var(--backdrop);
    font-family: "Poppins", sans-serif;
  }
  .card {
    position: absolute;
    left: 257px;
    width: 686px;
    height: 392px;
    background: var(--card);
    overflow: hidden;
  }
  .card-front { top: 165px; }
  .card-back { top: 653px; }

  .front-decor {
    position: absolute;
    left: -30px; top: 12px;
    width: 360px; height: 360px;
    border-radius: 50%;
    background: var(--faint-shape);
  }
  .front-brand {
    position: absolute;
    right: 35px; top: 312px;
    text-align: right;
  }
  .front-brand .brand-name {
    font-weight: 500;
    font-size: 31px;
    letter-spacing: 0.5px;
    color: var(--navy);
    line-height: 1;
  }
  .front-brand .brand-url {
    margin-top: 8px;
    font-family: "Roboto", sans-serif;
    font-size: 15px;
    letter-spacing: 3.2px;
    color: var(--grey-text);
  }

  .back-brand {
    position: absolute;
    left: 38px; top: 52px;
    display: flex; align-items: center; gap: 14px;
  }
  .back-brand .brand-dot {
    width: 62px; height: 62px;
    border-radius: 50%;
    background: var(--navy);
  }
  .back-brand .brand-name {
    font-weight: 500;
    font-size: 25px;
    letter-spacing: 0.4px;
    color: var(--navy);
  }
  .person {
    position: absolute;
    left: 35px; top: 223px;
  }
  .person-name {
    font-weight: 500;
    font-size: 24px;
    color: var(--navy);
    line-height: 1.1;
  }
  .person-role {
    font-size: 15px;
    color: var(--soft-grey);
    margin-top: 2px;
  }
  .contact {
    position: absolute;
    left: 35px; top: 286px;
    font-size: 16px;
    color: var(--grey-text);
    line-height: 21px;
  }
  .contact .address { margin-top: 7px; }
</style>
</head>
<body>
  <section class="card card-front">
    <div class="front-decor"></div>
    <div class="front-brand">
      <div class="brand-name">WARD COMPASS</div>
      <div class="brand-url">www.wardcompass.example</div>
    </div>
  </section>

  <section class="card card-back">
    <div class="back-brand">
      <span class="brand-dot"></span>
      <span class="brand-name">WARD COMPASS</span>
    </div>
    <div class="person">
      <div class="person-name">SALWA KETTANI</div>
      <div class="person-role">CEO</div>
    </div>
    <div class="contact">
      <div>P: +90 612 348 2175</div>
      <div>E: info@wardcompass.example W: wardcompass.example</div>
      <div class="address">14 Annakhil 7 H.R.B. Rabat, Morocco</div>
    </div>
  </section>
</body>
</html>
```